iPhone iOS 7 App For Managing Tasks/Photos for Internal Company Use

We need an app design that displays company objectives and task, and provides the interface for employees to complete a task by uploading a photo and adding comments.

Please see attached mock up sketches as a rough guideline

Final delivery of files must contain PSD, and all layers/objects sliced both is PSD and PNG files

Target Market(s)

This is a tool for internal employee use

Industry/Entity Type

It Company

Requirements
Must have
• Must include logo, and match the colour scheme
Use iPhone iOS 7 Style

```html
<!DOCTYPE html>
<html lang="en">
<head>
<meta charset="utf-8">
<title>Upload Task Photo</title>
<link rel="stylesheet" href="https://fonts.googleapis.com/css2?family=Open+Sans:wght@400;600;700&display=swap">
<style>
  :root {
    --bg: #a6b8c3;
    --header-bg: #ffffff;
    --brand: #4f6f75;
    --ink: #1a1a1a;
    --accent: #f07a5a;
    --accent-dark: #e8603f;
    --track: #e4e9eb;
    --panel: #8fa4ae;
    --panel-line: #7e939d;
    --panel-text: #587079;
    --nav-dark: #5b777d;
    --nav-face: #eef0f0;
    --nav-icon: #8b8f90;
    --label: #4d6a71;
  }
  * { margin: 0; padding: 0; box-sizing: border-box; }
  html, body { width: 675px; height: 1200px; overflow: hidden; }
  body {
    position: relative;
    background: var(--bg);
    font-family: "Open Sans", sans-serif;
  }
  .status-bar {
    position: absolute; top: 0; left: 0; width: 675px; height: 51px;
    color: var(--ink); font-size: 22px;
  }
  .status-bar .carrier { position: absolute; left: 12px; top: 8px; display: flex; align-items: center; gap: 6px; }
  .status-bar .time { position: absolute; left: 0; right: 0; top: 8px; text-align: center; font-weight: 600; }
  .status-bar .power { position: absolute; right: 12px; top: 8px; display: flex; align-items: center; gap: 8px; }
  .app-header {
    position: absolute; top: 51px; left: 0; width: 675px; height: 84px;
    background: var(--header-bg);
    box-shadow: 0 2px 4px rgba(0,0,0,.15);
    display: flex; align-items: center; justify-content: center; gap: 18px;
    color: var(--brand); font-weight: 600; font-size: 31px;
  }
  .app-header .brand { display: flex; align-items: center; gap: 8px; }
  .app-header .brand-dot { width: 14px; height: 14px; border-radius: 50%; background: var(--accent); }
  .upload-dial { position: absolute; left: 179px; top: 268px; }
  .upload-label {
    position: absolute; left: 0; width: 675px; top: 448px; text-align: center;
    color: var(--brand); font-weight: 700; font-size: 21px;
  }
  .comments {
    position: absolute; left: 95px; top: 636px; width: 524px; height: 209px;
    background: var(--panel); border: 1px solid var(--panel-line);
    border-bottom-color: #c7d3d9;
    color: var(--panel-text); font-size: 30px; padding: 20px 31px;
  }
  .save-button {
    position: absolute; left: 233px; top: 871px; width: 226px; height: 49px;
    background: #fff; border: 2px solid #d5dcdf; border-radius: 25px;
    color: var(--brand); font-family: inherit; font-weight: 700; font-size: 21px;
  }
  .tab-bar { position: absolute; left: 0; top: 1045px; }
  .tab-labels { position: absolute; top: 1140px; left: 0; width: 675px; height: 40px; }
  .tab-labels span {
    position: absolute; width: 160px; margin-left: -80px; text-align: center;
    color: var(--label); font-weight: 700; font-size: 26px;
  }
</style>
</head>
<body>
  <div class="status-bar">
    <div class="carrier">
      <svg width="62" height="14" viewBox="0 0 62 14" aria-hidden="true">
        <circle cx="6" cy="7" r="5.5" fill="#1a1a1a"/><circle cx="18" cy="7" r="5.5" fill="#1a1a1a"/><circle cx="30" cy="7" r="5.5" fill="#1a1a1a"/>
        <circle cx="42" cy="7" r="5" fill="none" stroke="#1a1a1a"/><circle cx="54" cy="7" r="5" fill="none" stroke="#1a1a1a"/>
      </svg>
      <span>NORTHLINK</span>
      <svg width="24" height="18" viewBox="0 0 24 18" aria-hidden="true">
        <path d="M12 17 L2 6 A15 15 0 0 1 22 6 Z" fill="#1a1a1a"/>
      </svg>
    </div>
    <div class="time">4:21 PM</div>
    <div class="power">
      <svg width="14" height="22" viewBox="0 0 14 22" aria-hidden="true">
        <path d="M2 6 L12 16 L7 21 V1 L12 6 L2 16" fill="none" stroke="#1a1a1a" stroke-width="1.8"/>
      </svg>
      <span>100%</span>
      <svg width="48" height="20" viewBox="0 0 48 20" aria-hidden="true">
        <rect x="1" y="1" width="42" height="18" rx="3" fill="none" stroke="#1a1a1a" stroke-width="1.5"/>
        <rect x="3.5" y="3.5" width="37" height="13" rx="1.5" fill="#1a1a1a"/>
        <rect x="44" y="6" width="3" height="8" fill="#1a1a1a"/>
      </svg>
    </div>
  </div>

  <header class="app-header">
    <div class="brand"><span class="brand-dot"></span><span>Veltra</span></div>
    <span>COMPANY NAME</span>
  </header>

  <svg class="upload-dial" width="332" height="332" viewBox="0 0 332 332" role="img" aria-label="Upload progress about half complete">
    <circle cx="166" cy="166" r="164" fill="#fff" stroke="#d4dbde" stroke-width="2"/>
    <circle cx="166" cy="166" r="139" fill="none" stroke="var(--track)" stroke-width="25"/>
    <circle cx="166" cy="166" r="139" fill="none" stroke="var(--accent)" stroke-width="25"
            stroke-dasharray="454 900" transform="rotate(-90 166 166)"/>
    <circle cx="166" cy="166" r="126" fill="#f6f6f6" stroke="#d8dcdd" stroke-width="2"/>
    <path d="M134 160 a14 14 0 0 1 6 -27 a20 20 0 0 1 38 -3 a15 15 0 0 1 18 30 Z" fill="var(--accent)"/>
    <path d="M166 130 l-9 10 h6 v12 h6 v-12 h6 Z" fill="#fff"/>
  </svg>
  <div class="upload-label">Uploading Image</div>

  <div class="comments">Comments</div>

  <button class="save-button">Save &amp; Complete</button>

  <svg class="tab-bar" width="675" height="100" viewBox="0 0 675 100" role="img" aria-label="Tab bar">
    <path d="M105 50 C150 35 219 35 264 50 C309 35 377 35 422 50 C467 35 537 35 582 50 C537 65 467 65 422 50 C377 65 309 65 264 50 C219 65 150 65 105 50 Z" fill="var(--nav-dark)"/>
    <g fill="var(--nav-dark)">
      <circle cx="105" cy="50" r="42"/><circle cx="264" cy="50" r="42"/><circle cx="422" cy="50" r="42"/><circle cx="582" cy="50" r="42"/>
    </g>
    <g fill="var(--nav-face)" stroke="#c9cfd0" stroke-width="1.5">
      <circle cx="105" cy="50" r="32"/><circle cx="264" cy="50" r="32"/><circle cx="422" cy="50" r="32"/><circle cx="582" cy="50" r="32"/>
    </g>
    <g fill="var(--nav-icon)">
      <path d="M85 50 L105 32 L125 50 H119 V67 H91 V50 Z"/>
      <rect x="100" y="53" width="10" height="14" fill="var(--nav-face)"/>
    </g>
    <g fill="none" stroke="var(--nav-icon)" stroke-width="4">
      <circle cx="260" cy="54" r="17"/><circle cx="260" cy="54" r="9"/>
      <path d="M260 54 L282 32"/>
    </g>
    <g fill="var(--nav-icon)">
      <path d="M404 50 L432 34 L438 58 L410 60 Z"/>
      <rect x="412" y="58" width="7" height="12" rx="2"/>
      <path d="M442 36 a12 12 0 0 1 4 18" fill="none" stroke="var(--nav-icon)" stroke-width="3"/>
    </g>
    <g fill="var(--nav-icon)">
      <path d="M566 30 H586 V36 H580 V64 H586 V70 H566 Z"/>
      <path d="M584 44 H592 V38 L603 50 L592 62 V56 H584 Z"/>
    </g>
  </svg>
  <nav class="tab-labels">
    <span style="left:100px">Home</span>
    <span style="left:269px">Objectives</span>
    <span style="left:417px">News</span>
    <span style="left:581px">Log Out</span>
  </nav>
</body>
</html>
```